Web Design Project

We wish to create a web based logistics exchange for heavy machinery and equipment catering to the mining, oil, gas and infrastructure industries. Customers interested in shipping equipment can post a load on the site and this would then be auctioned off through an online auction to prospective transport providers.Payments would be through direct bank transfer,pelko, quorvantix etc.
Both shippers and transport providers gain access via membership.
When a load is posted it would appear on the map indicating its location.Transport providers click on the icon of this map to access information of the pick up and delivery details as well as the load description.
The site would also have links to transport departments and equipment specification sites.
Advertising and merchandising are the other areas of revenue through the site

Target Market(s)

Shippers from Machinery Auction centres and Transport companies

Industry/Entity Type

Catering

Requirements
Must have
• The Logo of the company. The file is attached.

```html
<!DOCTYPE html>
<html lang="en">
<head>
<meta charset="utf-8">
<title>Haulridge – Heavy Machinery Logistics Exchange</title>
<link rel="stylesheet" href="https://fonts.googleapis.com/css2?family=Ubuntu:ital,wght@0,300;0,400;0,500;1,300&display=swap">
<style>
:root{
  --ink:#2e2e2e;
  --text:#3a3a3a;
  --muted:#9a9a9a;
  --page:#f4f4f4;
  --white:#ffffff;
  --line:#c9c9c9;
  --footer:#ececec;
  --blue:#2f86d6;
  --blue-dark:#1f5f9f;
  --sky-top:#6f9fd6;
  --sky-low:#cfdcea;
  --truck:#c83a35;
}
*{box-sizing:border-box;margin:0;padding:0}
html,body{width:979px;height:1200px;overflow:hidden}
body{position:relative;background:var(--page);font-family:"Ubuntu",sans-serif;color:var(--text)}
.abs{position:absolute}
.top-bar{left:0;top:0;width:979px;height:3px;background:#1b1b1b}
.header{left:0;top:3px;width:979px;height:92px;background:var(--white)}
.brand{left:98px;top:28px;display:flex;align-items:center;gap:8px;font-size:21px;font-weight:500;color:var(--ink);letter-spacing:1px}
.brand-dot{width:14px;height:14px;border-radius:50%;background:var(--blue)}
.account{left:650px;top:40px;font-size:11px;font-weight:500;color:var(--ink)}
.account span{color:var(--muted);font-weight:300}
.search{left:745px;top:35px;width:128px;height:20px;border:1px solid var(--line);border-radius:10px;background:var(--white)}
.round-btn{position:absolute;right:2px;top:2px;width:15px;height:15px;border-radius:50%;background:var(--blue);border:1px solid var(--blue-dark)}
.nav{top:66px;font-size:11px;color:#555}
.nav.current{font-weight:500;color:var(--ink)}
.hero{left:0;top:95px;width:979px;height:382px;background:linear-gradient(180deg,var(--sky-top) 0%,#a8c0dc 45%,var(--sky-low) 70%,#8c8f96 100%)}
.features{left:98px;top:425px;width:783px;height:114px;background:linear-gradient(#f2f2f2,#e2e2e2);border:1px solid #d6d6d6;border-radius:3px;box-shadow:0 6px 8px -6px rgba(0,0,0,.25)}
.feature-right{left:392px;top:0;width:390px;height:112px;background:#f3f3f3;border-left:1px solid #d9d9d9}
.icon{width:34px;height:34px}
.feature h2,.section-title{font-weight:400;color:var(--ink)}
.feature h2{font-size:16px}
.feature p{font-size:10.4px;line-height:12.6px;width:285px;margin-top:4px}
.btn{display:inline-block;width:106px;height:20px;border:1px solid #b9b9b9;border-radius:2px;background:linear-gradient(#fff,#e6e6e6);font-size:9.5px;font-weight:500;text-align:center;line-height:18px;color:var(--ink)}
.feature .btn{margin-top:5px}
.section-title{font-size:16px}
.body-copy{font-size:10.4px;line-height:12.6px}
.photo-frame{left:106px;top:755px;width:115px;height:91px;border:1px solid var(--line);background:var(--white);padding:5px}
.photo{width:100%;height:100%;background:linear-gradient(#d9dde2,#9aa2ac)}
.quote{left:228px;top:756px;width:250px}
.quote-by{left:228px;top:810px;font-size:10.4px;font-style:italic;font-weight:300;color:#777;line-height:13px}
.arrows{left:445px;top:830px;width:36px;height:16px;border:1px solid #aaa;border-radius:2px;background:linear-gradient(#fff,#e2e2e2);display:flex}
.arrows span{flex:1;display:flex;align-items:center;justify-content:center}
.arrows span+span{border-left:1px solid #aaa}
.video{left:498px;top:604px;width:375px;height:211px;background:linear-gradient(135deg,#4d5d78 0%,#2f3b50 55%,#1f2633 100%)}
.footer{left:0;top:988px;width:979px;height:212px;background:var(--footer)}
.f-col{top:1015px;font-size:9.4px;line-height:16.7px;color:var(--muted);font-weight:300}
.f-col h3{font-size:9.4px;font-weight:400;color:var(--ink)}
.newsletter{left:693px;top:1034px;width:180px;height:20px;border:1px solid var(--line);border-radius:10px;background:var(--white);font-size:9.4px;color:var(--muted);font-weight:300;padding:3px 9px}
.social{top:1085px;width:24px;height:24px;border-radius:2px;background:#b7bcc4}
.copyright{left:106px;top:1157px;font-size:9.4px;color:var(--muted);font-weight:300}
.copyright a{color:var(--ink);text-decoration:none;font-weight:400}
</style>
</head>
<body>
<div class="abs top-bar"></div>
<header class="abs header"></header>
<div class="abs brand"><span class="brand-dot"></span>HAULRIDGE</div>
<div class="abs account">Log In <span>or</span> Sign Up</div>
<div class="abs search"><span class="round-btn"></span></div>
<span class="abs nav current" style="left:552px">Home</span>
<span class="abs nav" style="left:607px">About Us</span>
<span class="abs nav" style="left:678px">How It Works</span>
<span class="abs nav" style="left:769px">Contact Us</span>
<span class="abs nav" style="left:848px">FAQs</span>

<div class="abs hero" role="img" aria-label="Red heavy-haul truck carrying a large industrial engine in front of snowy mountains"></div>

<section class="abs features">
  <svg class="abs icon" style="left:42px;top:42px" viewBox="0 0 34 34"><circle cx="17" cy="17" r="15" fill="#3f9ee0" stroke="#2a6fa8"/><path d="M9 12c4-3 8 0 9 3s5 4 5 8-4 6-7 5-1-5-4-7-4-6-3-9z" fill="#8fc34a"/></svg>
  <div class="abs feature" style="left:97px;top:16px">
    <h2>Get your Machinery Shipped</h2>
    <p>This is Photoshop's version of Lorem Ipsum. Proin gravida nibh vel velit auctor aliquet. Aenean sollicitudin, lorem quis bibendum auctor.</p>
    <span class="btn">Get Free Quotes</span>
  </div>
  <div class="abs feature-right">
    <svg class="abs icon" style="left:46px;top:42px" viewBox="0 0 34 34"><path d="M3 6l9-3 10 3 9-3v25l-9 3-10-3-9 3z" fill="#5cb85c" stroke="#2f7a34"/><path d="M12 3v25M22 6v25" stroke="#2f7a34"/><circle cx="10" cy="14" r="3" fill="#d9534f"/></svg>
    <div class="abs feature" style="left:97px;top:16px">
      <h2>Ship and Earn</h2>
      <p>This is Photoshop's version of Lorem Ipsum. Proin gravida nibh vel velit auctor aliquet. Aenean sollicitudin, lorem quis bibendum auctor.</p>
      <span class="btn">Start Bidding</span>
    </div>
  </div>
</section>

<h2 class="abs section-title" style="left:106px;top:573px">Welcome to Haulridge</h2>
<div class="abs body-copy" style="left:106px;top:604px;width:370px">
  <p>This is Photoshop's version of Lorem Ipsum. Proin gravida nibh vel velit auctor aliquet. Aenean sollicitudin, lorem quis bibendum auctor, nisi elit consequat ipsum, nec sagittis sem nibh id elit. Duis sed odio sit amet nibh vulputate cursus a sit amet mauris. Morbi accumsan ipsum velit.</p>
  <p style="margin-top:12px">Nam nec tellus a odio tincidunt auctor a ornare odio. Sed non mauris vitae erat consequat auctor eu in elit. Class aptent taciti sociosqu ad litora</p>
</div>

<h2 class="abs section-title" style="left:106px;top:723px">Testimonials</h2>
<div class="abs photo-frame"><div class="photo" role="img" aria-label="Portrait photo of the client giving the testimonial"></div></div>
<p class="abs body-copy quote">This is Photoshop's version of Lorem Ipsum. Proin gravida nibh vel velit auctor aliquet. Aenean sollicitudin, lorem quis bibendum auctor, nisi elit consequat ipsum, nec sagittis sem nibh id elit.</p>
<div class="abs quote-by">--<br>Dale Marsh<br>CEO Ridgeline Mines</div>
<div class="abs arrows">
  <span><svg width="5" height="7" viewBox="0 0 5 7"><path d="M5 0v7L0 3.5z" fill="#333"/></svg></span>
  <span><svg width="5" height="7" viewBox="0 0 5 7"><path d="M0 0v7l5-3.5z" fill="#333"/></svg></span>
</div>

<h2 class="abs section-title" style="left:499px;top:573px">How It Works</h2>
<div class="abs video" role="img" aria-label="Video still of the heavy-haul truck with its engine load">
  <svg class="abs" style="left:175px;top:90px" width="38" height="40" viewBox="0 0 38 40"><path d="M4 2l32 18L4 38z" fill="#fff" stroke="#fff" stroke-width="4" stroke-linejoin="round"/></svg>
</div>
<p class="abs body-copy" style="left:500px;top:827px;width:372px">This is Photoshop's version of Lorem Ipsum. Proin gravida nibh vel velit auctor aliquet. Aenean sollicitudin, lorem quis bibendum auctor, nisi elit consequat ipsum, nec sagittis sem nibh id elit. Duis sed odio sit amet nibh vulputate cursus a sit amet mauris. Morbi accumsan ipsum velit.</p>
<span class="abs btn" style="left:498px;top:887px">Learn More</span>

<footer class="abs footer"></footer>
<div class="abs f-col" style="left:106px"><h3>Why Us</h3>Features<br>Pricing<br>Site Gallery<br>Demo Video<br>Clients<br>Testimonials</div>
<div class="abs f-col" style="left:204px"><h3>Company</h3>About Us<br>Press<br>Careers<br>Contact Us<br>Partner with Us</div>
<div class="abs f-col" style="left:302px"><h3>Support</h3>Help<br>Contact Support<br>Video Tutorials<br>Privacy Policy<br>Terms of Service<br>Report Abuse</div>
<div class="abs f-col" style="left:398px"><h3>Community</h3>Blog<br>Forums<br>Affiliates</div>
<div class="abs f-col" style="left:498px"><h3>Contact Us</h3>14 Quarry Lane<br>Gravida nibh vel velit auctor aliquet<br>Aenean sollicitudin<br>Kalbarra<br><br>hello@haulridge.example<br>(300) 555 0142</div>
<div class="abs f-col" style="left:693px"><h3>Subscribe Newsletter</h3></div>
<div class="abs newsletter">email address<span class="round-btn"></span></div>
<div class="abs f-col" style="left:693px;top:1063px"><h3>Follow Us</h3></div>
<span class="abs social" style="left:693px" aria-label="Social network link"></span>
<span class="abs social" style="left:723px" aria-label="Social network link"></span>
<span class="abs social" style="left:752px" aria-label="Social network link"></span>
<span class="abs social" style="left:782px" aria-label="Social network link"></span>
<p class="abs copyright">Copyright 2013. All rights reserved. <a href="#">Privacy Policy</a> | <a href="#">Terms of Service</a></p>
</body>
</html>
```